Web design for financial services

A modern web design of financial services (brokerage firm)
Req.s and technology tags :
- Very mobile friendly.
- One paged with some inner pages.
- Animated sticky header .
- Member login area for e-trade.
- Support RTL language.
- HTML & CSS.

The logo will be Home link
• MPTR :
WHO WE ARE
Content :
i) Board of Directors
ii) Mission Statement
iii) Corporate Values
iv) Regulations
• Financial Services :
WHAT WE DO
Content:
i) Electronic trading
ii) Trading desk
iii) Institutional
iv) Investors Education
• News
• Market Tools
• Forms---- opens new page
• Careers---- opens new page
• Contact Us----opens new page

The website is :
http://www.mptr-doha-example.com/

The logo need some changes to be more modern and impressively , but with keeping same structure .

Some related websites :
https://www.lv-bourse.example/

financial market

Financial Service

Coded - Design and coding required

2 page

• same fonts of http://www.kwdholdings.example/

• - Very mobile friendly.
• - One paged with some inner pages.
• - Animated sticky header .
• - Member login area for e-trade.
• - Support RTL language.
• - HTML & CSS.
• Slider , some Qatari theme,
• i like the video inside the home page
• ex :http://www.kwdholdings.example/

```html
<!DOCTYPE html>
<html lang="en">
<head>
<meta charset="utf-8">
<title>MPTR – Financial Services</title>
<link href="https://fonts.googleapis.com/css2?family=Oswald:wght@500;600&family=Roboto:wght@300;400;500;700&display=swap" rel="stylesheet">
<style>
:root{
  --red:#a3231f;
  --red-dark:#8c1b18;
  --ink:#333;
  --text:#666;
  --muted:#8a8a8a;
  --light:#f2f2f2;
  --card:#ebebeb;
  --white:#fff;
  --black:#111;
  --band:#2a2a2a;
}
*{box-sizing:border-box;margin:0;padding:0}
html,body{width:1200px;height:4100px;overflow:hidden}
body{font-family:"Roboto",Arial,sans-serif;color:var(--text);background:var(--white);position:relative}
section,header,footer{position:absolute;left:0;width:1200px}
a{color:inherit;text-decoration:none}
.btn{display:inline-block;background:var(--red);color:var(--white);font-size:21px;font-weight:500;text-transform:uppercase;padding:0 22px;line-height:56px;border-radius:3px}
.sec-title{text-align:center;font-size:46px;font-weight:400;color:#7a7a7a;letter-spacing:1px;text-transform:uppercase}
.sec-title b{color:var(--red);font-weight:500}
.lorem{font-size:14px;line-height:23px;color:var(--text)}
.more{font-size:13px;font-weight:700;color:var(--red-dark);text-decoration:underline;font-style:italic}

/* header + hero */
.hero{top:0;height:680px;background:linear-gradient(180deg,#dfe3e7 0%,#c7ced6 40%,#b8c0c9 62%,#8f98a2 100%)}
.hero-photo{position:absolute;inset:0;background:linear-gradient(90deg,rgba(255,255,255,.25),rgba(120,130,145,.2) 70%,rgba(80,90,100,.25))}
.site-header{top:0;height:130px;z-index:2}
.brand{position:absolute;left:80px;top:38px;display:flex;align-items:center;gap:10px;font-size:40px;font-weight:700;color:var(--red)}
.brand i{width:18px;height:18px;background:var(--red);display:block}
.login{position:absolute;right:80px;top:18px;display:flex;align-items:center;gap:10px;font-size:15px;color:var(--ink)}
.lang{border:1px solid #999;background:#fff;padding:3px 8px;font-size:13px}
.lang-arrow{width:30px;height:30px;background:var(--red);display:flex;align-items:center;justify-content:center}
.main-nav{position:absolute;right:80px;top:60px;display:flex;align-items:center;gap:28px;font-size:15px;color:var(--ink);text-transform:uppercase}
.main-nav .active{background:var(--red);color:var(--white);padding:12px 22px;border-radius:2px;margin-right:10px}
.hero-title{position:absolute;left:78px;top:275px;font-family:"Oswald",Arial,sans-serif;font-weight:600;font-size:78px;color:#1b1b1b;letter-spacing:-1px;text-transform:uppercase}
.hero-text{position:absolute;left:78px;top:375px;width:680px;font-size:17px;line-height:25px;color:#222}
.hero .btn{position:absolute;left:78px;top:460px}

/* welcome */
.welcome{top:680px;height:415px}
.welcome h2{position:absolute;left:78px;top:58px;font-size:48px;font-weight:400;color:#7a7a7a}
.welcome h2 b{color:var(--red);font-weight:500}
.welcome .lorem{position:absolute;left:78px;top:122px;width:650px}
.welcome .btn{position:absolute;left:78px;top:290px;font-size:18px;line-height:52px}
.video{position:absolute;left:753px;top:65px;width:369px;height:280px;background:linear-gradient(135deg,#c9d3de,#7d8a99 60%,#55606c)}
.video svg{position:absolute;left:145px;top:100px}

/* who we are */
.who{top:1095px;height:560px;background:var(--light)}
.who .sec-title{position:absolute;top:52px;width:100%}
.who .intro{position:absolute;top:118px;left:180px;width:840px;text-align:center}
.pillar{position:absolute;width:220px}
.pillar h3{font-size:16px;font-weight:400;color:var(--ink);text-transform:uppercase;margin-bottom:8px}
.pillar .lorem{font-size:13.5px;line-height:22px}
.pillar.left{text-align:right}
.hexbadge{position:absolute}

/* careers */
.careers{top:1655px;height:195px;background:linear-gradient(90deg,#2b2b2b,#3d3d3d 55%,#2a2a2a)}
.careers h2{position:absolute;left:80px;top:38px;font-size:42px;font-weight:400;color:var(--red)}
.careers p{position:absolute;left:80px;top:93px;width:760px;font-size:14px;line-height:23px;color:#bbb}
.careers .btn{position:absolute;right:80px;top:68px;font-size:18px;line-height:52px}

/* what we do */
.what{top:1850px;height:590px}
.what .sec-title{position:absolute;top:50px;width:100%}
.what .sub{position:absolute;top:112px;width:100%;text-align:center;font-size:17px;color:var(--ink)}
.service{position:absolute;top:160px;width:250px;height:365px;background:var(--card);text-align:center}
.service .thumb{margin:8px 8px 0;height:155px}
.service h3{font-size:16px;font-weight:400;color:var(--ink);margin:22px 0 8px;text-transform:uppercase}
.service .lorem{font-size:13.5px;line-height:22px;padding:0 18px;margin-bottom:12px}

/* testimonials */
.clients{top:2440px;height:395px;background:linear-gradient(90deg,#8e1f1c,#a8302b 45%,#9a2824);}
.clients h2{position:absolute;top:50px;width:100%;text-align:center;font-size:46px;font-weight:400;color:#d79b98;text-transform:uppercase}
.clients h2 b{color:var(--white);font-weight:500}
.clients .name{position:absolute;top:125px;width:100%;text-align:center;font-size:17px;color:#e6b7b4;text-transform:uppercase}
.quote-box{position:absolute;left:153px;top:160px;width:894px;height:115px;border:1px solid rgba(255,255,255,.55);padding:22px 50px;text-align:center;font-size:14px;line-height:24px;color:#fff}
.arrow-btn{position:absolute;top:198px;width:40px;height:40px;background:#fff;display:flex;align-items:center;justify-content:center}
.dots{position:absolute;top:310px;width:100%;display:flex;justify-content:center;gap:16px}
.dots i{width:12px;height:12px;border-radius:50%;background:#fff;display:block}
.dots i.on{background:#444}

/* news */
.news{top:2835px;height:595px}
.news .sec-title{position:absolute;top:52px;width:100%}
.post{position:absolute;top:125px;width:332px;height:410px;background:var(--card)}
.post .thumb{height:200px}
.date{position:absolute;left:10px;top:170px;width:85px;height:100px;background:var(--red);color:#fff;text-align:center;padding-top:8px}
.date b{display:block;font-size:40px;font-weight:500;line-height:46px}
.date span{font-size:15px}
.post h3{position:absolute;left:112px;top:218px;width:210px;font-size:15px;font-weight:700;color:var(--ink);line-height:23px}
.post .lorem{position:absolute;left:12px;top:290px;width:310px;font-size:13.5px;line-height:22px}
.post .more{position:absolute;left:12px;top:370px}

/* market tools */
.tools{top:3430px;height:315px;background:linear-gradient(180deg,#eef1f4,#d9dee4)}
.tools .sec-title{position:absolute;top:42px;width:100%;color:#666}
.tool{position:absolute;top:105px;width:220px;text-align:center}
.tool p{font-size:19px;font-weight:500;color:var(--black);text-transform:uppercase;margin-top:6px}
.tool.red p{color:var(--red)}

/* footer */
.site-footer{top:3745px;height:355px;background:var(--black);color:#ccc}
.foot-brand{position:absolute;left:120px;top:115px;font-size:64px;font-weight:700;color:#fff;display:flex;align-items:center;gap:16px}
.foot-brand i{width:26px;height:26px;background:var(--red);display:block}
.foot-col{position:absolute;top:35px}
.foot-col h4{font-size:18px;font-weight:500;color:var(--red);text-transform:uppercase;margin-bottom:12px;letter-spacing:1px}
.foot-col li{list-style:none;font-size:14px;line-height:24px;color:#ddd}
.foot-col li::before{content:"» ";color:var(--red)}
.contact-line{display:flex;gap:12px;font-size:14px;line-height:22px;margin-bottom:14px;color:#ddd}
.socials{display:flex;gap:10px}
.socials i{width:34px;height:34px;border-radius:50%;background:var(--red);display:block}
.foot-col input{width:245px;height:40px;border:0;padding:0 10px;font-size:14px;margin:12px 0;font-family:inherit}
.foot-col .btn{font-size:17px;line-height:44px;padding:0 30px}
.copyright{position:absolute;left:0;bottom:0;width:100%;height:72px;background:var(--red);text-align:center;line-height:72px;font-size:14px;color:#fff}
</style>
</head>
<body>

<section class="hero">
  <div class="hero-photo" role="img" aria-label="Businessman looking over a city skyline from a glass balcony"></div>
  <h1 class="hero-title">MPTR Financial Services</h1>
  <p class="hero-text">Lorem Ipsum is simply dummy text of the printing and typesetting industry. Lorem Ipsum has been the industry's standard dummy text ever since.</p>
  <a class="btn" href="#">Contact Us</a>
</section>

<header class="site-header">
  <a class="brand" href="#"><i></i>MPTR</a>
  <div class="login">
    <svg width="14" height="16" viewBox="0 0 14 16"><rect x="1" y="7" width="12" height="9" fill="#a3231f"/><path d="M3.5 7V4.5a3.5 3.5 0 0 1 7 0V7" stroke="#a3231f" stroke-width="2" fill="none"/></svg>
    <span>Login</span>
    <span class="lang">Eng</span>
    <span class="lang-arrow"><svg width="12" height="8"><path d="M0 0h12L6 8z" fill="#fff"/></svg></span>
  </div>
  <nav class="main-nav">
    <a class="active" href="#">MPTR</a>
    <a href="#">Financial Services</a>
    <a href="#">News</a>
    <a href="#">Market Tool</a>
    <a href="#">Forms</a>
    <a href="#">Careers</a>
    <a href="#">Contact Us</a>
  </nav>
</header>

<section class="welcome">
  <h2>WELCOME TO <b>MPTR</b></h2>
  <div class="lorem">
    <p>Lorem Ipsum is simply dummy text of the printing and typesetting industry. Lorem Ipsum has been the industry's standard dummy text ever since the 1500s, when an unknown.</p><br>
    <p>Lorem Ipsum is simply dummy text of the printing and typesetting industry. Lorem Ipsum has been the industry's standard dummy text ever since the 1500s, when an unknown printer took a galley of type and scrambled it to make a type specimen book. It has survived not only five centuries, but also the leap into electronic typesetting, remaining essentially.</p>
  </div>
  <a class="btn" href="#">Know More</a>
  <div class="video" role="img" aria-label="Video still of business people in a meeting with charts">
    <svg width="80" height="80" viewBox="0 0 80 80"><circle cx="40" cy="40" r="36" fill="none" stroke="#fff" stroke-width="5"/><path d="M31 24v32l26-16z" fill="#fff"/></svg>
  </div>
</section>

<section class="who">
  <h2 class="sec-title">Who <b>We Are</b></h2>
  <p class="intro lorem">Lorem Ipsum is simply dummy text of the printing and typesetting industry. Lorem Ipsum has been the industry's standard dummy text ever since the 1500s, when an unknown printer took a galley.</p>

  <div class="pillar left" style="left:198px;top:200px"><h3>Board of Directors</h3><p class="lorem">Lorem Ipsum is simply dummy text of the printing and typesetting industry. Lorem Ipsum has been the.</p><a class="more" href="#">READ MORE</a></div>
  <div class="pillar left" style="left:198px;top:365px"><h3>Mission Statement</h3><p class="lorem">Lorem Ipsum is simply dummy text of the printing and typesetting industry. Lorem Ipsum has been the.</p><a class="more" href="#">READ MORE</a></div>
  <div class="pillar" style="left:776px;top:200px"><h3>Regulations</h3><p class="lorem">Lorem Ipsum is simply dummy text of the printing and typesetting industry. Lorem Ipsum has been the.</p><a class="more" href="#">READ MORE</a></div>
  <div class="pillar" style="left:776px;top:365px"><h3>Corporate Values</h3><p class="lorem">Lorem Ipsum is simply dummy text of the printing and typesetting industry. Lorem Ipsum has been the.</p><a class="more" href="#">READ MORE</a></div>

  <svg class="hexbadge" style="left:440px;top:182px" width="150" height="150" viewBox="0 0 150 150"><polygon points="75,6 136,40 136,110 75,144 14,110 14,40" fill="#e9e9e9" stroke="#8a8a8a" stroke-width="8"/><polygon points="75,28 118,52 118,98 75,122 32,98 32,52" fill="#a3231f"/><circle cx="75" cy="64" r="10" fill="#fff"/><path d="M55 98c0-14 9-22 20-22s20 8 20 22z" fill="#fff"/></svg>
  <svg class="hexbadge" style="left:608px;top:182px" width="150" height="150" viewBox="0 0 150 150"><polygon points="75,6 136,40 136,110 75,144 14,110 14,40" fill="#e9e9e9" stroke="#8a8a8a" stroke-width="8"/><polygon points="75,28 118,52 118,98 75,122 32,98 32,52" fill="#a3231f"/><rect x="56" y="58" width="38" height="40" fill="none" stroke="#fff" stroke-width="5"/><path d="M64 70h22M64 80h22M64 90h14" stroke="#fff" stroke-width="4"/></svg>
  <svg class="hexbadge" style="left:440px;top:345px" width="150" height="150" viewBox="0 0 150 150"><polygon points="75,6 136,40 136,110 75,144 14,110 14,40" fill="#e9e9e9" stroke="#8a8a8a" stroke-width="8"/><polygon points="75,28 118,52 118,98 75,122 32,98 32,52" fill="#a3231f"/><circle cx="75" cy="75" r="24" fill="none" stroke="#fff" stroke-width="5"/><circle cx="75" cy="75" r="12" fill="none" stroke="#fff" stroke-width="5"/><circle cx="75" cy="75" r="4" fill="#fff"/></svg>
  <svg class="hexbadge" style="left:608px;top:345px" width="150" height="150" viewBox="0 0 150 150"><polygon points="75,6 136,40 136,110 75,144 14,110 14,40" fill="#e9e9e9" stroke="#8a8a8a" stroke-width="8"/><polygon points="75,28 118,52 118,98 75,122 32,98 32,52" fill="#a3231f"/><path d="M50 72l14-12 22 6 14 10-14 14-14-10" fill="none" stroke="#fff" stroke-width="5" stroke-linejoin="round"/></svg>
</section>

<section class="careers" role="img" aria-label="Dim city office towers behind the careers banner">
  <h2>CAREERS</h2>
  <p>Lorem Ipsum is simply dummy text of the printing and typesetting industry. Lorem Ipsum has been the industry's standard dummy text ever since the 1500s, when an unknown printer took a galley.</p>
  <a class="btn" href="#">Contact Us</a>
</section>

<section class="what">
  <h2 class="sec-title">What <b>We Do</b></h2>
  <p class="sub">Financial Services</p>
  <article class="service" style="left:80px"><div class="thumb" role="img" aria-label="Trader at multiple market screens" style="background:linear-gradient(135deg,#4a5560,#202830)"></div><h3>Electronic Trading</h3><p class="lorem">Lorem Ipsum is simply dummy text of the printing and typesetting industry Lorem Ipsum print text has been the.</p><a class="more" href="#">READ MORE</a></article>
  <article class="service" style="left:344px"><div class="thumb" role="img" aria-label="Open-plan trading desk with monitors" style="background:linear-gradient(135deg,#d8dcdf,#8a9097)"></div><h3>Trading Desk</h3><p class="lorem">Lorem Ipsum is simply dummy text of the printing and typesetting industry Lorem Ipsum print text has been the.</p><a class="more" href="#">READ MORE</a></article>
  <article class="service" style="left:608px"><div class="thumb" role="img" aria-label="Hand holding a rising blue bar chart" style="background:linear-gradient(135deg,#eef4f8,#8fb6d4)"></div><h3>Institutional</h3><p class="lorem">Lorem Ipsum is simply dummy text of the printing and typesetting industry Lorem Ipsum print text has been the.</p><a class="more" href="#">READ MORE</a></article>
  <article class="service" style="left:872px"><div class="thumb" role="img" aria-label="Presenter teaching investors in a meeting room" style="background:linear-gradient(135deg,#dfe2e5,#6f7780)"></div><h3>Investors Education</h3><p class="lorem">Lorem Ipsum is simply dummy text of the printing and typesetting industry Lorem Ipsum print text has been the.</p><a class="more" href="#">READ MORE</a></article>
</section>

<section class="clients" role="img" aria-label="Red tinted financial chart background">
  <h2>What Our <b>Client Say</b></h2>
  <p class="name">Client Name</p>
  <blockquote class="quote-box">"Lorem Ipsum is simply dummy text of the printing and typesetting industry. Lorem Ipsum has been the industry's standard dummy text ever since the 1500s, when an unknown printer took a galley of type and scrambled it to make a type specimen book. It has survived not only five centuries."</blockquote>
  <span class="arrow-btn" style="left:130px"><svg width="10" height="14"><path d="M9 1L2 7l7 6" stroke="#333" stroke-width="2" fill="none"/></svg></span>
  <span class="arrow-btn" style="left:1027px"><svg width="10" height="14"><path d="M1 1l7 6-7 6" stroke="#333" stroke-width="2" fill="none"/></svg></span>
  <div class="dots"><i></i><i></i><i class="on"></i></div>
</section>

<section class="news">
  <h2 class="sec-title">Latest <b>News</b></h2>
  <article class="post" style="left:78px"><div class="thumb" role="img" aria-label="Team reviewing charts in an office" style="background:linear-gradient(135deg,#e8ecef,#9aa5ae)"></div><div class="date"><b>02</b><span>Feb</span></div><h3>Lorem Ipsum is the simply dummy text of the.</h3><p class="lorem">Lorem Ipsum is simply dummy text of the printing and typesetting industry. Lorem Ipsum has been the industry's standard.</p><a class="more" href="#">KNOW MORE</a></article>
  <article class="post" style="left:434px"><div class="thumb" role="img" aria-label="Traders pointing at screens" style="background:linear-gradient(135deg,#6a7c90,#2c3540)"></div><div class="date"><b>02</b><span>Feb</span></div><h3>Lorem Ipsum is the simply dummy text of the.</h3><p class="lorem">Lorem Ipsum is simply dummy text of the printing and typesetting industry. Lorem Ipsum has been the industry's standard.</p><a class="more" href="#">KNOW MORE</a></article>
  <article class="post" style="left:790px"><div class="thumb" role="img" aria-label="Hand touching a digital graph" style="background:linear-gradient(135deg,#c5d6e6,#3f6d96)"></div><div class="date"><b>01</b><span>Jan</span></div><h3>Lorem Ipsum is the simply dummy text of the.</h3><p class="lorem">Lorem Ipsum is simply dummy text of the printing and typesetting industry. Lorem Ipsum has been the industry's standard.</p><a class="more" href="#">KNOW MORE</a></article>
</section>

<section class="tools" role="img" aria-label="Faded stock chart and pen background">
  <h2 class="sec-title">Market <b>Tools</b></h2>
  <div class="tool" style="left:230px"><svg width="90" height="90" viewBox="0 0 90 90"><polygon points="45,4 83,25 83,65 45,86 7,65 7,25" fill="#fff" stroke="#8a8a8a" stroke-width="6"/><text x="45" y="57" text-anchor="middle" font-family="Roboto,sans-serif" font-size="34" fill="#a3231f">1</text></svg><p>Active Company</p></div>
  <div class="tool red" style="left:490px"><svg width="90" height="90" viewBox="0 0 90 90"><polygon points="45,4 83,25 83,65 45,86 7,65 7,25" fill="#fff" stroke="#a3231f" stroke-width="6"/><text x="45" y="57" text-anchor="middle" font-family="Roboto,sans-serif" font-size="34" fill="#a3231f">2</text></svg><p>Top Company</p><svg width="16" height="14"><path d="M2 1l6 5 6-5M2 7l6 5 6-5" stroke="#a3231f" stroke-width="2" fill="none"/></svg></div>
  <div class="tool" style="left:745px"><svg width="90" height="90" viewBox="0 0 90 90"><polygon points="45,4 83,25 83,65 45,86 7,65 7,25" fill="#fff" stroke="#8a8a8a" stroke-width="6"/><text x="45" y="57" text-anchor="middle" font-family="Roboto,sans-serif" font-size="34" fill="#333">3</text></svg><p>Top Loser</p></div>
</section>

<footer class="site-footer">
  <a class="foot-brand" href="#"><i></i>MPTR</a>
  <div class="foot-col" style="left:345px">
    <h4>Sitemap</h4>
    <ul><li>MPTR</li><li>Financial Services</li><li>News</li><li>Market Tool</li><li>Forms</li><li>Careers</li><li>Contact Us</li></ul>
  </div>
  <div class="foot-col" style="left:610px;width:230px">
    <h4>Get In Touch</h4>
    <div class="contact-line"><svg width="16" height="20" viewBox="0 0 16 20"><path d="M8 0a7 7 0 0 1 7 7c0 5-7 13-7 13S1 12 1 7a7 7 0 0 1 7-7z" fill="#a3231f"/><circle cx="8" cy="7" r="2.5" fill="#111"/></svg><span>MPTR<br>101 - Lorem ipsum is simple dummy text of print &amp;type.</span></div>
    <div class="contact-line"><svg width="16" height="16" viewBox="0 0 16 16"><path d="M3 1l3 3-2 2c1 2 3 4 5 5l2-2 3 3-2 3C6 15 1 10 0 3z" fill="#a3231f"/></svg><span>+974-4000-1234</span></div>
    <div class="contact-line"><svg width="18" height="14" viewBox="0 0 18 14"><rect width="18" height="14" fill="#a3231f"/><path d="M1 1l8 6 8-6" stroke="#111" stroke-width="1.5" fill="none"/></svg><span>complaints@mptr-doha-example.com</span></div>
    <div class="socials"><i></i><i></i><i></i></div>
  </div>
  <div class="foot-col" style="left:875px;width:250px">
    <h4>Newsletter</h4>
    <p style="font-size:14px;line-height:22px;color:#ddd">Would you like to receive exclusive access to articles, white papers and our regular monthly newsletter?</p>
    <input type="text" placeholder="Enter Email Id">
    <a class="btn" href="#">Submit</a>
  </div>
  <div class="copyright">© MPTR - 2017. All Rights Reserved</div>
</footer>

</body>
</html>
```